Corporate Business Card

Very professional, Modern, Not to busy, include phone address email, website
(555) 617-4930, 18761 52nd Avenue S, Millbrook, OR 98047, martin@plumlinegroup.com, varkoworks.com

Target Market(s)

Manufacturing

Industry/Entity Type

Aero, machining, manufacturing, Off road racing

Contact Information for Business Card

Phone, address email, website

```html
<!DOCTYPE html>
<html lang="en">
<head>
<meta charset="utf-8">
<title>Varko Works — Business Card</title>
<link href="https://fonts.googleapis.com/css2?family=Mulish:wght@400;600;800&display=swap" rel="stylesheet">
<style>
  :root {
    --navy: #17356e;
    --red: #d8232a;
    --white: #ffffff;
    --backdrop: #232323;
  }
  * { margin: 0; padding: 0; box-sizing: border-box; }
  html, body { width: 1200px; height: 988px; overflow: hidden; }
  body {
    background: var(--backdrop);
    font-family: "Mulish", sans-serif;
    position: relative;
  }
  .card {
    position: absolute;
    width: 700px;
    height: 400px;
    border-radius: 22px;
    overflow: hidden;
    background: var(--navy);
  }
  .card-back { left: 250px; top: 52px; }
  .card-front { left: 250px; top: 536px; }

  .brand-name {
    font-weight: 800;
    letter-spacing: 3px;
    text-transform: uppercase;
    white-space: nowrap;
  }
  .card-back .brand-name {
    position: absolute;
    left: 0; right: 0; top: 168px;
    text-align: center;
    font-size: 56px;
    color: var(--white);
  }
  .card-back .brand-rule {
    position: absolute;
    left: 190px; top: 260px;
    width: 320px; height: 2px;
    background: var(--white);
  }

  .front-art { position: absolute; inset: 0; }
  .card-front .brand-name {
    position: absolute;
    left: 360px; top: 156px;
    width: 330px;
    text-align: center;
    font-size: 34px;
    color: var(--navy);
  }
  .card-front .brand-rule {
    position: absolute;
    left: 400px; top: 212px;
    width: 200px; height: 2px;
    background: var(--navy);
  }

  .contact {
    position: absolute;
    left: 64px; top: 150px;
    color: var(--white);
  }
  .person-name {
    font-size: 24px;
    font-weight: 800;
    color: var(--red);
    letter-spacing: 1px;
    text-transform: uppercase;
  }
  .person-role {
    font-size: 15px;
    font-weight: 600;
    letter-spacing: 1px;
    margin-bottom: 30px;
  }
  .address { font-size: 15px; line-height: 1.35; margin-bottom: 30px; }
  .details { list-style: none; font-size: 15px; line-height: 1.5; }
  .details li { display: flex; align-items: center; gap: 10px; }
  .details svg { width: 13px; height: 13px; fill: var(--red); flex: none; }
</style>
</head>
<body>

  <section class="card card-back" aria-label="Card back">
    <p class="brand-name">Varko Works</p>
    <span class="brand-rule" aria-hidden="true"></span>
  </section>

  <section class="card card-front" aria-label="Card front">
    <svg class="front-art" viewBox="0 0 700 400" aria-hidden="true">
      <circle cx="585" cy="185" r="262" fill="var(--red)"/>
      <circle cx="595" cy="180" r="254" fill="var(--white)"/>
    </svg>
    <p class="brand-name">Varko Works</p>
    <span class="brand-rule" aria-hidden="true"></span>

    <div class="contact">
      <p class="person-name">Daniel Reyes</p>
      <p class="person-role">FOUNDER</p>
      <p class="address">18761 52nd Avenue S,<br>Millbrook, OR 98047</p>
      <ul class="details">
        <li>
          <svg viewBox="0 0 24 24"><path d="M6.6 10.8a15 15 0 0 0 6.6 6.6l2.2-2.2c.3-.3.7-.4 1-.2 1.1.4 2.3.6 3.6.6.6 0 1 .4 1 1V20c0 .6-.4 1-1 1A17 17 0 0 1 3 4c0-.6.4-1 1-1h3.5c.6 0 1 .4 1 1 0 1.3.2 2.5.6 3.6.1.3 0 .7-.2 1z"/></svg>
          (555) 617-4930
        </li>
        <li>
          <svg viewBox="0 0 24 24"><path d="M2 5h20v14H2z M2 5l10 8 10-8" /></svg>
          martin@plumlinegroup.com
        </li>
        <li>
          <svg viewBox="0 0 24 24"><circle cx="12" cy="12" r="10"/></svg>
          www.varkoworks.com
        </li>
      </ul>
    </div>
  </section>

</body>
</html>
```